Valdane Companies Business Card Design

We need a new business card for our Private Equity Real Estate Development firm, “Valdane” and our EB-5 regional center “Thornmere Regional Center” on one card. We prefer a design that is simple, elegant, and represents the luxury products we design and build as well as the financial security and stability our successful history has produced. We are an industry leader in our field and 3rd generation family business that has evolved into an institutional quality investment platform. Considered design size is standard business card dimensions (3.5 x 2 inches with an additional 1/8 inch space for design elements or backgrounds that extend beyond the finished size of your piece.

Target Market(s)

• High net worth individuals
• Highly skilled technical workers and physicians in the US seeking investment-based immigration opportunities
• Sophisticated private equity investors
• Intermediary partners include domestic attorneys and investment brokers, as well as international agent networks
• US real estate developers

Industry/Entity Type

Finance

Contact Information for Business Card

(Providing placeholder info for personal information, please design for longer character spaces, longer names and addresses etc..)
• Logo for Valdane
• Logo for Thornmere Regional Center
• Full name: Marcus Valdane
• Job title: CEO
• Email address: mvaldane@valdanecompanies.com
• Cell phone number: +1.555.314.2287
• Office number +1.555.628.4410
• Office address: Larkfield Court 5, 4817 Vista Orilla, San Ramon, CA.
• Website: www.valdanecompanies.com

Font styles to use
Serif
Sans Serif

Colors
ec1f27
ffffff
000000

Requirements
Must have
• • Logo for Valdane
• • Logo for Thornmere Regional Center
• - Use rounded corners
• (See .ai file included for logos)
Nice to have
• • Simple, elegant design
• • Aesthetically compatible with our website design (www.valdanecompanies.com)
• • Color palette including but not limited to white, black, and red (as per logos)
Should not have
• - Not too much red color
• - Do not stack both logos on top of each other

```html
<!DOCTYPE html>
<html lang="en">
<head>
<meta charset="utf-8">
<title>Valdane Companies Business Card</title>
<link href="https://fonts.googleapis.com/css2?family=Libre+Baskerville:wght@400;700&family=Lato:wght@400&display=swap" rel="stylesheet">
<style>
  :root {
    --backdrop: #636363;
    --card: #2e2e2e;
    --silver: #c4c4c4;
    --ink: #f2f2f2;
    --muted: #e2e2e2;
    --rule: #6a6a6a;
  }
  * { margin: 0; padding: 0; box-sizing: border-box; }
  html, body { width: 1200px; height: 1200px; overflow: hidden; }
  body {
    background: var(--backdrop);
    position: relative;
    font-family: "Lato", Arial, sans-serif;
  }
  .card {
    position: absolute;
    left: 246px;
    width: 706px;
    height: 403px;
    background: var(--card);
    border-radius: 26px;
    box-shadow: 0 8px 16px rgba(0,0,0,0.25);
  }
  .card--front { top: 138px; }
  .card--back { top: 646px; }

  .brand {
    position: absolute;
    display: flex;
    align-items: center;
    gap: 14px;
    font-family: "Libre Baskerville", Georgia, serif;
    font-weight: 400;
    color: var(--silver);
    white-space: nowrap;
  }
  .brand__mark {
    background: var(--silver);
    flex: none;
  }
  .card--front .brand {
    left: 0; right: 0; top: 170px;
    justify-content: center;
    font-size: 40px;
  }
  .card--front .brand__mark { width: 34px; height: 34px; }

  .card--back .brand {
    left: 60px; top: 172px;
    width: 250px;
    font-size: 22px;
    line-height: 1.25;
  }
  .card--back .brand__mark { width: 26px; height: 26px; }
  .card--back .brand__name { display: block; }

  .divider {
    position: absolute;
    left: 334px; top: 84px;
    width: 1px; height: 222px;
    background: var(--rule);
  }
  .contact {
    position: absolute;
    left: 352px; top: 80px;
    color: var(--ink);
  }
  .contact__name {
    font-family: "Libre Baskerville", Georgia, serif;
    font-weight: 700;
    font-size: 24px;
    letter-spacing: 0.5px;
    line-height: 1.2;
  }
  .contact__title {
    font-size: 19px;
    margin-top: 4px;
    color: var(--muted);
  }
  .contact__address {
    font-size: 16px;
    line-height: 25px;
    margin-top: 14px;
    color: var(--muted);
  }
  .contact__list {
    list-style: none;
    margin-top: 14px;
    font-size: 16px;
    color: var(--muted);
  }
  .contact__list li {
    display: flex;
    align-items: center;
    height: 23.5px;
  }
  .contact__list svg {
    width: 15px; height: 15px;
    margin-right: 18px;
    fill: none;
    stroke: var(--ink);
    stroke-width: 1.6;
  }
</style>
</head>
<body>

<section class="card card--front">
  <div class="brand">
    <span class="brand__mark"></span>
    <span class="brand__name">Valdane Capital</span>
  </div>
</section>

<section class="card card--back">
  <div class="brand">
    <span class="brand__mark"></span>
    <span class="brand__name">Thornmere<br>Regional Center</span>
  </div>

  <div class="divider"></div>

  <div class="contact">
    <h1 class="contact__name">MARCUS VALDANE</h1>
    <p class="contact__title">CEO</p>
    <p class="contact__address">Larkfield Court 5, 4817 Vista Orilla<br>San Ramon, CA.</p>
    <ul class="contact__list">
      <li>
        <svg viewBox="0 0 16 16" aria-hidden="true"><path d="M4 1.5l2.2 3.2-1.4 1.6c.8 2 2.4 3.6 4.4 4.4l1.6-1.4 3.2 2.2-1.2 2.5C7 13.5 2.5 9 1.5 3z" fill="#f2f2f2" stroke="none"/></svg>
        <span>+1.555.314.2287</span>
      </li>
      <li>
        <svg viewBox="0 0 16 16" aria-hidden="true"><rect x="4" y="1" width="8" height="14" rx="1.5"/><line x1="7" y1="12.5" x2="9" y2="12.5"/></svg>
        <span>+1.555.628.4410</span>
      </li>
      <li>
        <svg viewBox="0 0 16 16" aria-hidden="true"><rect x="1" y="3.5" width="14" height="9" fill="#f2f2f2" stroke="none"/><path d="M1 3.5l7 5 7-5" stroke="#2e2e2e"/></svg>
        <span>mvaldane@valdanecompanies.com</span>
      </li>
      <li>
        <svg viewBox="0 0 16 16" aria-hidden="true"><circle cx="8" cy="8" r="6.5"/><ellipse cx="8" cy="8" rx="2.8" ry="6.5"/><line x1="1.5" y1="8" x2="14.5" y2="8"/></svg>
        <span>www.valdanecompanies.com</span>
      </li>
    </ul>
  </div>
</section>

</body>
</html>
```